Vorelan.com Personal Trainer/Fitness Website

I want a website to market my personal training/Outdoor Bootcamp Class services, as well as to ditribute nutrivex. I need a logo as well I included an address for the Harbor Gales 1975 logo. I'd like Vorelan in place of Harbor Gales, and in Black and white, just different enough so I can't get sued by the PBL.
https://www.pictofind.example/imgres?imgurl=http%3A%2F%2Fwww.darnell-quibury.example%2Fwp-content%2Fuploads%2F2014%2F01%2Fgales_logo4.jpg&imgrefurl=http%3A%2F%2Fwww.darnell-quibury.example%2Fpbl-logo-redesigns-harbor-gales%2F&docid=_qkwzR7TBAgXpL&tbnid=m4tpU8KdOXjnRP%3A&w=600&h=450&client=ms-android-carrier&bih=512&biw=360&ved=0ahUKEwiRtpgyp9HMAhUTwGMKHRPMBWMQMwg6KBQwFA&iact=mrc&uact=8.
It should be about 5 pages 1. home 2. about 3. Services 4. Blog/Videos and programs 5. Contact.
http://www.dorvinfitness.example.uk/ is a website I like the style of.

Target Market(s)

Seattle area

Industry/Entity Type

Fitness

Coding

Coded - Design and coding required

Number of Pages Required

4 page

Font styles to use
Serif
Sans Serif

Requirements
Must have
• A minimal look
Nice to have
• A logo similar to the 1975 Harbor Galewinds Logo, with a Small Milo Brandt ripping his shirt open(with a picture of the logo on his shirt, picture within picture) to turn into Ironjaw in the center. Skyline is black, Background and small figure white(with black logo on shirt)

```html
<!DOCTYPE html>
<html lang="en">
<head>
<meta charset="utf-8">
<title>Vorelan – Personal Training &amp; Outdoor Bootcamp</title>
<link rel="stylesheet" href="https://fonts.googleapis.com/css2?family=Jost:ital,wght@0,400;0,500;0,600;1,400&display=swap">
<style>
:root{
  --ink:#111111;
  --text:#2b2b2b;
  --muted:#6a6a6a;
  --white:#ffffff;
  --about-bg:#e9ebf0;
  --card-bg:#eceef2;
  --arrow-box:#b9bcc2;
  --footer-bg:#2f2f30;
  --footer-bar:#1f1f20;
  --footer-line:#5b5b5b;
  --footer-text:#d8d8d8;
  --tab-bg:#c9cacc;
  --accent:#2f6f5a;
  --sun:#fff3c8;
  --grass:#8fae4e;
  --leaf:#55733a;
  --skin:#a8704f;
  --shirt:#2f5aa8;
}
*{box-sizing:border-box;margin:0;padding:0}
html,body{width:1200px;height:2571px;overflow:hidden}
body{position:relative;background:var(--white);font-family:"Jost",sans-serif;color:var(--text)}

/* header */
.site-header{position:absolute;left:0;top:0;width:1200px;height:110px;background:var(--white);border-bottom:1px solid #cfcfcf}
.brand{position:absolute;left:104px;top:14px;display:flex;align-items:center;gap:10px}
.brand-dot{width:56px;height:56px;border-radius:50%;background:var(--ink)}
.brand-name{font-size:26px;font-weight:600;letter-spacing:2px;color:var(--ink)}
.social{position:absolute;display:flex;gap:10px}
.social span{width:27px;height:27px;background:#555b63;display:block}
.call{position:absolute;left:902px;top:20px;display:flex;align-items:center;gap:12px}
.call-icon{width:34px;height:34px;border-radius:50%;border:1.5px solid var(--ink);display:flex;align-items:center;justify-content:center}
.call small{display:block;font-size:10px;letter-spacing:.5px;color:var(--muted)}
.call strong{display:block;font-size:23px;font-weight:400;letter-spacing:1px;color:var(--ink);line-height:1}
.call-divider{position:absolute;left:888px;top:22px;width:1px;height:36px;background:#cfcfcf}
.main-nav{position:absolute;top:76px;left:0;width:1200px}
.main-nav a{position:absolute;font-size:12px;font-weight:500;color:var(--ink);text-decoration:none;letter-spacing:.3px}
.main-nav .active::after{content:"";position:absolute;left:-2px;right:-2px;top:30px;height:3px;background:var(--accent)}

/* hero */
.hero{position:absolute;left:0;top:110px;width:1200px;height:445px;
  background:
    radial-gradient(ellipse 300px 220px at 170px 40px,var(--sun) 0%,rgba(255,243,200,0) 100%),
    radial-gradient(ellipse 260px 190px at 1050px 90px,#6f9a38 0%,rgba(111,154,56,0) 100%),
    radial-gradient(ellipse 150px 260px at 590px 120px,#4b4f55 0%,rgba(75,79,85,0) 100%),
    radial-gradient(ellipse 200px 80px at 920px 370px,var(--shirt) 0%,rgba(47,90,168,0) 100%),
    radial-gradient(ellipse 520px 120px at 760px 330px,var(--skin) 0%,rgba(168,112,79,0) 100%),
    radial-gradient(ellipse 340px 90px at 330px 370px,#3a3a3a 0%,rgba(58,58,58,0) 100%),
    linear-gradient(180deg,#d8cfa6 0%,#b8b87c 40%,#9fb25a 70%,#7c9a3e 100%)}
.hero-title{position:absolute;left:100px;top:176px;background:rgba(20,20,20,.82);color:var(--white);font-size:30px;font-weight:500;line-height:36px;padding:6px 10px;letter-spacing:.5px}
.btn{position:absolute;display:flex;align-items:center;justify-content:space-between;font-size:13px;font-weight:600;text-decoration:none}
.btn-light{background:var(--white);color:var(--ink)}
.btn-dark{background:var(--ink);color:var(--white)}
.btn .arr{width:20px;height:20px}

/* section titles */
.section-title{position:absolute;left:0;width:1200px;text-align:center;font-size:31px;font-weight:500;color:var(--ink)}
.section-title::after{content:"";display:block;width:80px;height:1px;background:#9a9a9a;margin:12px auto 0}

/* about */
.about{position:absolute;left:0;top:555px;width:1200px;height:328px;background:var(--about-bg)}
.about-photo{position:absolute;left:120px;top:30px;width:300px;height:298px;
  background:
    radial-gradient(ellipse 40px 50px at 150px 50px,#b98563 0%,rgba(185,133,99,0) 100%),
    radial-gradient(ellipse 150px 170px at 150px 210px,#a8704f 0%,#b98563 45%,rgba(233,235,240,0) 100%)}
.about-title{position:absolute;left:462px;top:40px;font-size:31px;font-weight:500;color:var(--ink);display:flex;align-items:center;gap:14px}
.about-title::after{content:"";width:88px;height:1px;background:#9a9a9a;margin-top:10px}
.about-text{position:absolute;left:464px;top:92px;width:640px;font-size:12.6px;line-height:28.5px;color:var(--text)}

/* services */
.service-card{position:absolute;top:1007px;width:276px;height:293px;background:var(--card-bg)}
.service-photo{width:276px;height:150px}
.service-card h3{font-size:20px;font-weight:500;color:var(--ink);margin:16px 0 0 19px}
.service-card p{font-size:12.6px;line-height:22px;margin:8px 16px 0 19px;color:var(--text)}
.arrow-box{position:absolute;right:0;bottom:0;width:36px;height:34px;background:var(--arrow-box);display:flex;align-items:center;justify-content:center}

/* videos band */
.videos{position:absolute;left:0;top:1418px;width:1200px;height:430px;
  background:
    radial-gradient(ellipse 420px 200px at 920px 140px,#f7f8f9 0%,rgba(247,248,249,0) 100%),
    linear-gradient(90deg,#d8d9db 0%,#eceded 35%,#e2e3e5 70%,#d3d4d6 100%)}
.videos-photo{position:absolute;left:30px;top:98px;width:225px;height:332px;
  background:
    radial-gradient(ellipse 45px 55px at 100px 50px,#4a3326 0%,rgba(74,51,38,0) 100%),
    radial-gradient(ellipse 120px 180px at 110px 230px,#b9babd 0%,#c7c8ca 55%,rgba(216,217,219,0) 100%),
    radial-gradient(ellipse 70px 120px at 40px 160px,#5a3d2c 0%,rgba(90,61,44,0) 100%)}
.videos-list{position:absolute;left:305px;top:148px;list-style:none;font-size:12.6px;line-height:27.5px;color:var(--text)}
.videos-list li::before{content:"";display:inline-block;width:5px;height:5px;background:var(--text);margin:0 10px 2px 0;vertical-align:middle}
.video-frame{position:absolute;left:755px;top:150px;width:346px;height:205px;border:3px solid #4d4d4d;
  background:
    radial-gradient(ellipse 80px 60px at 60px 40px,#eef2d8 0%,rgba(238,242,216,0) 100%),
    radial-gradient(ellipse 160px 40px at 200px 140px,#5d6f86 0%,rgba(93,111,134,0) 100%),
    linear-gradient(180deg,#a9c27a 0%,#86a553 55%,#6f8f3e 100%)}
.play{position:absolute;left:148px;top:78px;width:46px;height:46px}
.link-more{position:absolute;left:862px;top:376px;font-size:14px;font-weight:600;color:var(--ink);display:flex;align-items:center;gap:8px}

/* blog */
.blog-card{position:absolute;top:1978px;width:477px;height:207px;background:var(--card-bg)}
.blog-photo{position:absolute;left:0;top:0;width:206px;height:207px}
.blog-body{position:absolute;left:220px;top:14px;width:250px}
.blog-body h3{font-size:17px;font-weight:600;line-height:21px;color:var(--ink)}
.blog-body time{display:block;font-size:12px;font-style:italic;color:var(--muted);margin-top:8px}
.blog-body p{font-size:12.6px;line-height:22px;margin-top:6px}

/* footer */
.site-footer{position:absolute;left:0;top:2254px;width:1200px;height:281px;background:var(--footer-bg);color:var(--footer-text)}
.footer-col h4{position:absolute;font-size:18px;font-weight:500;color:var(--white);padding-bottom:10px;border-bottom:1px solid var(--footer-line)}
.quick-links{position:absolute;left:102px;top:73px;list-style:none;font-size:13px;line-height:29px}
.quick-links li::before{content:"";display:inline-block;width:6px;height:6px;border:2px dotted var(--footer-text);margin-right:10px;vertical-align:middle}
.contact-list{position:absolute;left:307px;top:74px;list-style:none;font-size:13px;line-height:22px}
.contact-list li{display:flex;gap:12px;margin-bottom:7px}
.contact-list svg{flex:none;margin-top:3px}
.field{position:absolute;left:576px;width:217px;background:var(--white);font-size:10px;color:#888;padding:5px 8px}
.footer-brand{position:absolute;left:858px;top:60px;width:222px;height:170px;border-radius:111px 111px 0 0;background:#cfd0d2;display:flex;align-items:flex-end;justify-content:center;padding-bottom:30px}
.footer-brand span{font-size:26px;font-weight:600;letter-spacing:2px;color:var(--footer-bg)}
.footer-bar{position:absolute;left:0;top:2535px;width:1200px;height:36px;background:var(--footer-bar)}
.copyright{position:absolute;left:100px;top:11px;font-size:12px;color:var(--footer-text)}
.follow-tab{position:absolute;left:780px;top:0;width:420px;height:36px;background:var(--tab-bg);border-radius:24px 0 0 0}
.follow-tab b{position:absolute;left:54px;top:7px;font-size:17px;font-weight:500;color:var(--ink)}
</style>
</head>
<body>

<header class="site-header">
  <div class="brand"><span class="brand-dot"></span><span class="brand-name">VORELAN</span></div>
  <div class="social" style="left:722px;top:24px"><span></span><span></span><span></span><span></span></div>
  <div class="call-divider"></div>
  <div class="call">
    <div class="call-icon">
      <svg width="16" height="16" viewBox="0 0 24 24"><path d="M6.6 10.8a15 15 0 0 0 6.6 6.6l2.2-2.2c.3-.3.7-.4 1-.2 1.1.4 2.3.6 3.6.6.6 0 1 .4 1 1V20c0 .6-.4 1-1 1A17 17 0 0 1 3 4c0-.6.4-1 1-1h3.5c.6 0 1 .4 1 1 0 1.3.2 2.5.6 3.6.1.3 0 .7-.2 1z" fill="#111"/></svg>
    </div>
    <div><small>CALL US NOW :</small><strong>012. 345. 6789</strong></div>
  </div>
  <nav class="main-nav">
    <a class="active" style="left:407px">HOME</a>
    <a style="left:505px">ABOUT</a>
    <a style="left:605px">SERVICES</a>
    <a style="left:722px">BLOG</a>
    <a style="left:814px">VIDEOS AND PROGRAMS</a>
    <a style="left:1033px">CONTACT</a>
  </nav>
</header>

<section class="hero" role="img" aria-label="Group of people doing sit-ups outdoors on sunlit grass with a trainer standing behind">
  <h1 class="hero-title">GET FIT! GET STRONG!<br>GET OUTDOORS!</h1>
  <a class="btn btn-light" style="left:100px;top:272px;width:148px;height:38px;padding:0 12px 0 14px">Get Started
    <svg class="arr" viewBox="0 0 20 20"><circle cx="10" cy="10" r="10" fill="#111"/><path d="M6 10h7M10 6.5l3.5 3.5L10 13.5" stroke="#fff" stroke-width="2" fill="none"/></svg></a>
</section>

<section class="about">
  <div class="about-photo" role="img" aria-label="Smiling muscular trainer standing with hands on hips"></div>
  <h2 class="about-title">About Vorelan</h2>
  <p class="about-text">Lorem ipsum dolor sit amet, consectetuer adipiscing elit, sed diam nonummy nibh euismod tincid laoreet dolore magna aliquam erat volutpat. Ut wisi enim ad minim veniam, quis nostrud exerci tati ullamcorper suscipit lobortis nisl ut aliquip ex ea commodo consequat. Duis autem vel eum iriure dolor in hendreri in vulputate velit esse molestie consequat, vel illum dolore eu feugiat nulla facilisis at vero eros et accumsan et iusto odio dignissim qui blandit praesent luptatum zzril dolore te feugait...</p>
  <a class="btn btn-dark" style="left:465px;top:248px;width:150px;height:40px;padding:0 12px 0 16px">Learn More
    <svg class="arr" viewBox="0 0 20 20"><circle cx="10" cy="10" r="10" fill="#fff"/><path d="M6 10h7M10 6.5l3.5 3.5L10 13.5" stroke="#111" stroke-width="2" fill="none"/></svg></a>
</section>

<h2 class="section-title" style="top:920px">Our Services</h2>

<article class="service-card" style="left:122px">
  <div class="service-photo" role="img" aria-label="Trainer coaching a client stretching in a park" style="background:radial-gradient(ellipse 60px 70px at 90px 40px,#6f8a5a 0%,rgba(111,138,90,0) 100%),radial-gradient(ellipse 40px 75px at 225px 80px,#34496e 0%,rgba(52,73,110,0) 100%),radial-gradient(ellipse 70px 25px at 120px 110px,#2c2c2c 0%,rgba(44,44,44,0) 100%),linear-gradient(180deg,#9db98a 0%,#7c9d5e 60%,#8fb35a 100%)"></div>
  <h3>Personal Training</h3>
  <p>Magna aliquam erat volutpat. Ut niml ad minim veniam, quis naullamcorper suscipit commodo consequat.</p>
  <span class="arrow-box"><svg width="12" height="14" viewBox="0 0 12 14"><path d="M3 2l6 5-6 5" stroke="#fff" stroke-width="2.5" fill="none"/></svg></span>
</article>
<article class="service-card" style="left:459px">
  <div class="service-photo" role="img" aria-label="Outdoor bootcamp group doing sit-ups on grass" style="background:radial-gradient(ellipse 50px 50px at 240px 20px,#f3a45a 0%,rgba(243,164,90,0) 100%),radial-gradient(ellipse 60px 40px at 60px 90px,#3bb0a8 0%,rgba(59,176,168,0) 100%),radial-gradient(ellipse 150px 35px at 150px 90px,#b98468 0%,rgba(185,132,104,0) 100%),linear-gradient(180deg,#b9cf7e 0%,#93b561 55%,#7fa54c 100%)"></div>
  <h3>Outdoor Bootcamp</h3>
  <p>Magna aliquam erat volutpat. Ut niml ad minim veniam, quis naullamcorper suscipit commodo consequat.</p>
  <span class="arrow-box"><svg width="12" height="14" viewBox="0 0 12 14"><path d="M3 2l6 5-6 5" stroke="#fff" stroke-width="2.5" fill="none"/></svg></span>
</article>
<article class="service-card" style="left:797px">
  <div class="service-photo" role="img" aria-label="Small group training with push-ups outdoors" style="background:radial-gradient(ellipse 110px 50px at 110px 40px,#a9705a 0%,rgba(169,112,90,0) 100%),radial-gradient(ellipse 30px 70px at 215px 70px,#2f3b56 0%,rgba(47,59,86,0) 100%),radial-gradient(ellipse 60px 40px at 40px 25px,#c64a36 0%,rgba(198,74,54,0) 100%),linear-gradient(180deg,#7e9a5c 0%,#9aae72 55%,#c9c4a2 100%)"></div>
  <h3>Small Group</h3>
  <p>Magna aliquam erat volutpat. Ut niml ad minim veniam, quis naullamcorper suscipit commodo consequat.</p>
  <span class="arrow-box"><svg width="12" height="14" viewBox="0 0 12 14"><path d="M3 2l6 5-6 5" stroke="#fff" stroke-width="2.5" fill="none"/></svg></span>
</article>
<a class="btn btn-dark" style="left:501px;top:1335px;width:198px;height:42px;padding:0 12px 0 16px">View All Services
  <svg class="arr" viewBox="0 0 20 20"><circle cx="10" cy="10" r="10" fill="#fff"/><path d="M6 10h7M10 6.5l3.5 3.5L10 13.5" stroke="#111" stroke-width="2" fill="none"/></svg></a>

<section class="videos" role="img" aria-label="Bright gym interior with large windows">
  <h2 class="section-title" style="top:48px">Videos And Programs</h2>
  <div class="videos-photo" role="img" aria-label="Trainer in a gym holding a clipboard and pen"></div>
  <ul class="videos-list">
    <li>Lorem ipsum dolor sit amet, consectetur adipiscing elit.</li>
    <li>Cras sagittis neque at nulla congue, a pulvinar turpis .</li>
    <li>Nunc consequat tortor id lorem mattis egestas.</li>
    <li>Suspendisse tristique leo sit amet magna consequat &nbsp;vitae dolor.</li>
    <li>Aliquam placerat dui sit amet nunc vehicula, et nisl sodales.</li>
    <li>Morbi faucibus metus vel erat pharetra accumsan.</li>
    <li>Nullam finibus tellus vitae ipsum tincidunt laoreet.</li>
    <li>Morbi et magna elementum, lobortis risus non, &nbsp;arcu.</li>
  </ul>
  <div class="video-frame" role="img" aria-label="Video preview of an outdoor bootcamp session">
    <svg class="play" viewBox="0 0 46 46"><circle cx="23" cy="23" r="21" fill="rgba(255,255,255,.35)" stroke="#111" stroke-width="2.5"/><path d="M18 14l13 9-13 9z" fill="#111"/></svg>
  </div>
  <div class="link-more">View All Videos
    <svg width="18" height="18" viewBox="0 0 20 20"><circle cx="10" cy="10" r="10" fill="#111"/><path d="M6 10h7M10 6.5l3.5 3.5L10 13.5" stroke="#fff" stroke-width="2" fill="none"/></svg></div>
</section>

<h2 class="section-title" style="top:1890px">Latest Blog</h2>

<article class="blog-card" style="left:98px">
  <div class="blog-photo" role="img" aria-label="Woman doing push-ups on grass in a park" style="background:radial-gradient(ellipse 60px 40px at 70px 90px,#9fdc5a 0%,rgba(159,220,90,0) 100%),radial-gradient(ellipse 50px 50px at 60px 50px,#b07a5a 0%,rgba(176,122,90,0) 100%),linear-gradient(180deg,#a7c98a 0%,#6fa84a 50%,#3f7d2a 100%)"></div>
  <div class="blog-body">
    <h3>Magna aliquam erat volutpal<br>Ut niml ad minim</h3>
    <time>Posted May &nbsp;12th, 2016</time>
    <p>Lorem ipsum dolor sit a consectetuer adipiscing elit,sed diam nonumm nibh euismod tincid laoreet d magnaautem praesent luptatum feugait...</p>
  </div>
  <span class="arrow-box"><svg width="12" height="14" viewBox="0 0 12 14"><path d="M3 2l6 5-6 5" stroke="#fff" stroke-width="2.5" fill="none"/></svg></span>
</article>
<article class="blog-card" style="left:623px">
  <div class="blog-photo" role="img" aria-label="Trainer measuring a client's waist in a studio" style="background:radial-gradient(ellipse 50px 30px at 70px 110px,#e0568c 0%,rgba(224,86,140,0) 100%),radial-gradient(ellipse 60px 110px at 70px 110px,#b07a5e 0%,rgba(176,122,94,0) 100%),radial-gradient(ellipse 50px 110px at 160px 110px,#d9dbe0 0%,rgba(217,219,224,0) 100%),linear-gradient(135deg,#1e1e1e,#3a3230)"></div>
  <div class="blog-body">
    <h3>Magna aliquam erat volutpal<br>Ut niml ad minim</h3>
    <time>Posted May &nbsp;12th, 2016</time>
    <p>Lorem ipsum dolor sit a consectetuer adipiscing elit,sed diam nonumm nibh euismod tincid laoreet d magnaautem praesent luptatum feugait...</p>
  </div>
  <span class="arrow-box"><svg width="12" height="14" viewBox="0 0 12 14"><path d="M3 2l6 5-6 5" stroke="#fff" stroke-width="2.5" fill="none"/></svg></span>
</article>

<footer class="site-footer">
  <div class="footer-col"><h4 style="left:102px;top:32px;width:128px">Quick Links</h4></div>
  <ul class="quick-links">
    <li>Home</li><li>About Us</li><li>Services</li><li>Blog</li><li>Contact</li>
  </ul>
  <div class="footer-col"><h4 style="left:307px;top:32px;width:196px">Contact Us</h4></div>
  <ul class="contact-list">
    <li><svg width="12" height="15" viewBox="0 0 12 16"><path d="M6 0a6 6 0 0 0-6 6c0 4.5 6 10 6 10s6-5.5 6-10a6 6 0 0 0-6-6zm0 8.5A2.5 2.5 0 1 1 6 3.5a2.5 2.5 0 0 1 0 5z" fill="#ddd"/></svg><span>Lorem ipsum dolor sit amet,<br>consectetuer, NC1234</span></li>
    <li><svg width="13" height="13" viewBox="0 0 24 24"><path d="M6.6 10.8a15 15 0 0 0 6.6 6.6l2.2-2.2c.3-.3.7-.4 1-.2 1.1.4 2.3.6 3.6.6.6 0 1 .4 1 1V20c0 .6-.4 1-1 1A17 17 0 0 1 3 4c0-.6.4-1 1-1h3.5c.6 0 1 .4 1 1 0 1.3.2 2.5.6 3.6.1.3 0 .7-.2 1z" fill="#ddd"/></svg><span>123. 456. 7890</span></li>
    <li><svg width="13" height="13" viewBox="0 0 16 16"><rect x="4" y="1" width="8" height="4" fill="#ddd"/><rect x="1" y="6" width="14" height="6" rx="1" fill="#ddd"/><rect x="4" y="10" width="8" height="5" fill="#ddd" stroke="#2f2f30"/></svg><span>123. 456. 7890</span></li>
    <li><svg width="13" height="11" viewBox="0 0 16 12"><rect width="16" height="12" rx="1" fill="#ddd"/><path d="M1 1l7 6 7-6" stroke="#2f2f30" stroke-width="1.5" fill="none"/></svg><span>info@vorelan.com</span></li>
  </ul>
  <div class="footer-col"><h4 style="left:576px;top:32px;width:214px">Quick Contact</h4></div>
  <div class="field" style="top:106px;height:30px">Name</div>
  <div class="field" style="top:145px;height:46px">Message</div>
  <a class="btn btn-dark" style="left:576px;top:217px;width:110px;height:32px;padding:0 8px 0 12px;font-size:13px">SUBMIT
    <svg class="arr" viewBox="0 0 20 20"><circle cx="10" cy="10" r="10" fill="#fff"/><path d="M6 10h7M10 6.5l3.5 3.5L10 13.5" stroke="#111" stroke-width="2" fill="none"/></svg></a>
  <div class="footer-brand"><span>VORELAN</span></div>
</footer>

<div class="footer-bar">
  <p class="copyright">© 2016. <b>VORELAN</b>. All Right Reserved</p>
  <div class="follow-tab">
    <b>Follow Us :</b>
    <div class="social" style="left:170px;top:5px"><span></span><span></span><span></span><span></span></div>
  </div>
</div>

</body>
</html>
```